Flyer-Design für Musikverein - Jugendkapelle
Zielgruppe
Musikverein Kolmsried
Unsere Zielgruppe sind Kinder und Jugendliche, die ein Instrument erlernen wollen.
Der Einstieg der jüngsten geht in einem Alter ab ca. 8 Jahren los. Die meisten neuen Musiker steigen zwischen 10 - 14 Jahren ein.
Der Flyer soll aber auch geeignet sein um an Grund- und weiterführenden Schulen ausgelegt werden zu können um Musiker für die Jugendkapelle zu gewinnen. Dementsprechend frisch und interessant soll der Flyer gestaltet sein.
Aufgabenstellung
Es soll ansprechend sein für Jugendliche, frisch, fröhlich und soll das Interesse der jugendlichen mit dem Design wecken.
Es soll die Jugendlichkeit, die Blasmusik und das Vereinsleben miteinander verbinden, sowie die Vorteile und der Spaß an der Musik (Instrument erlernen, Spaß am Musizieren, neue Freunde und Kameradschaft und auch Freizeitaktivitäten) miteinander darstellen.

```html
<!DOCTYPE html>
<html lang="de">
<head>
<meta charset="utf-8">
<title>Jugendkapelle KLANGFUNKE – Musikverein Kolmsried</title>
<link href="https://fonts.googleapis.com/css2?family=Work+Sans:wght@400;800&family=Caveat+Brush&display=swap" rel="stylesheet">
<style>
  :root {
    --bg: #f9c555;
    --white: #ffffff;
    --accent: #e8692a;
    --highlight: #fcdc5c;
    --wash-light: #f6a15a;
    --wash-dark: #ef8731;
    --icon: #fbeedd;
  }
  html, body { margin: 0; padding: 0; overflow: hidden; }
  body { width: 1200px; height: 2572px; background: var(--bg); }
  .flyer {
    position: relative; width: 1200px; height: 2572px; overflow: hidden;
    background: var(--bg); color: var(--white);
    font-family: "Work Sans", Arial, sans-serif;
  }
  .flyer > * { position: absolute; margin: 0; white-space: nowrap; }
  b, strong { font-weight: 800; }
  .body-text {
    left: 109px; font-size: 38px; line-height: 52px;
    letter-spacing: 2.2px; font-weight: 400;
  }
  .intro { top: 164px; }
  .orchestra { top: 423px; }
  .question {
    top: 708px; left: 109px;
    font-size: 46px; line-height: 60px; font-weight: 800; letter-spacing: 0.8px;
  }
  .invite {
    top: 1008px; left: 109px;
    font-size: 51px; line-height: 64px; font-weight: 800; color: var(--accent);
  }
  .band-name-wrap { position: relative; z-index: 0; }
  .band-name { position: relative; color: var(--white); }
  .band-name::before {
    content: ""; position: absolute; left: -20px; right: -24px; top: 4px; bottom: -8px;
    background: var(--highlight); z-index: -1; transform: rotate(-0.6deg);
  }
  .instrument-icon { left: 568px; top: 1253px; width: 98px; height: 149px; }
  .wash { left: 0; top: 1500px; width: 1200px; height: 920px; }
  .info-title {
    top: 1505px; left: 109px; font-family: "Caveat Brush", cursive;
    font-size: 106px; line-height: 110px; letter-spacing: 1px; font-weight: 400;
  }
  .website { top: 1655px; }
  .contact-intro { top: 1872px; }
  .board-label { top: 2028px; left: 109px; font-size: 40px; font-weight: 800; letter-spacing: 0.8px; }
  .address { top: 2098px; line-height: 57px; }
  .reach { top: 2305px; line-height: 57px; }
  .welcome-tag {
    left: 634px; top: 1960px; width: 464px; height: 168px;
    background: var(--highlight); transform: rotate(-6deg);
    font-family: "Caveat Brush", cursive; font-size: 84px; line-height: 66px;
    text-align: center; display: flex; align-items: center; justify-content: center;
  }
</style>
</head>
<body>
<main class="flyer">
  <p class="body-text intro">In unserer Jugendkapelle haben die <b>Kinder</b><br><b>und Jugendlichen</b> die Möglichkeit, nach <b>1 bis</b><br><b>2-jähriger Ausbildung</b> in der Gruppe zu spie-<br>len und zu üben.</p>
  <p class="body-text orchestra">Danach geht es an das Musizieren im <b>großen</b><br><b>Orchester.</b> Letztendlich entscheiden die Diri-<br>genten und Ausbilder über den Eintritt in die<br>jeweiligen Orchester.</p>
  <p class="question">Oder du kannst schon ein Instrument<br>spielen und willst mit anderen gemein-<br>sam musizieren?</p>
  <p class="invite">Dann komm doch in die<br>Jugendkapelle <span class="band-name-wrap"><span class="band-name">„KLANGFUNKE“</span></span></p>

  <div class="instrument-icon" role="img" aria-label="Kleines Tuba-Symbol">
    <svg width="98" height="149" viewBox="0 0 98 149"><ellipse cx="52" cy="90" rx="38" ry="56" fill="var(--icon)"/></svg>
  </div>

  <svg class="wash" viewBox="0 0 1200 920" aria-hidden="true">
    <defs>
      <linearGradient id="washGrad" x1="0" y1="0" x2="1" y2="1">
        <stop offset="0" stop-color="var(--wash-light)"/>
        <stop offset="1" stop-color="var(--wash-dark)"/>
      </linearGradient>
    </defs>
    <path d="M88 113 L311 76 L580 149 L933 221 L1200 253 L1200 900 L1037 854 L726 802 L477 761 L342 667 L207 522 L104 346 L73 201 Z" fill="url(#washGrad)"/>
  </svg>

  <h2 class="info-title">Nähere Informationen:</h2>
  <p class="body-text website">auf unserer Homepage unter:<br><b>www.kolmsried-musikverein.de</b></p>
  <p class="body-text contact-intro">Oder kontaktiert<br>uns direkt:</p>
  <p class="board-label">Jugendvorstand:</p>
  <p class="body-text address">Lena Hartwig<br>Lindenweg 7<br>72999 Kolmsried</p>
  <p class="body-text reach">Tel.: 0170 5 55 01 23<br>E-Mail: lena.hartwig@postfach-xz.de</p>

  <p class="welcome-tag">Wir freuen uns<br>auf Euch!</p>
</main>
</body>
</html>
```